Blow Dry Bar Business Cards

These cards must be eye catching and modern.
You must be willing to work fast and make changes.

Winner will be offered other projects

Files 1 THIS IS THE STYLE CARDS I AM INTRESTED IN!!!
Please be creative, I am paying for my own eye catching design. I need files to be nexa press ready.

COLORS THAT ARE PAINTED INSIDE MY SHOP:
- - - http://www.quorvelpaint.example/en/explore-colors/painter/color-selector.html?colors=4007-3C

- - - http://www.brandivex.example/color/paint-colors/hidden-corridor-d58-2

I want the business cards sleek and modern if you use the logo please correct imperfections. I added the part that says Blow Dry Bar (see website).
Do not be afraid to separate the blow dryer from the name to make the cards look like the file with the pink elephant.

SHOULD INCLUDE
*Blow Dryer (we are a blow dry bar not a salon we do not cut or color so do not include sheers of any kind)
*BUSINESS NAME: Simply Swept Upward - Blow Dry Bar (PLEASE SEE MY WEBSITE)
* Website: SIMPLYSWEPTUPWARD.EXAMPLE
*Phone number (555) 014-2763
Updates

Nexa press said it can be submitted in JPG

http://www.brandivex.example/color/paint-colors/hidden-corridor-d58-2 http://www.quorvelpaint.example/en/explore-colors/painter/color-selector.html?colors=4007-3C ^^^^ These links will take you to the color paint that is painted inside my shop.

Target Market(s)

AGES 18 - 55 WOMEN
HIGH END MARKET

Industry/Entity Type

Salon

Requirements
Must have
• SEE COLOR EXAMPLE FILE
BLOW DRYER
UNIQUE
I LIKE THE CARD WITH THE PINK ELEPHANT THE BEST
Nice to have
• BE AS CREATIVE AND MODERN AS POSSIBLE DO NOT COPY ANY OF THE CARDS BELOW.
Should not have
• SCISSORS
PINK

```html
<!DOCTYPE html>
<html lang="en">
<head>
<meta charset="utf-8">
<title>Simply Swept Upward – Blow Dry Bar Business Cards</title>
<link rel="stylesheet" href="https://fonts.googleapis.com/css2?family=Roboto:wght@300;400&display=swap">
<style>
  :root {
    --page-bg: #e9e6e1;
    --card-bg: #191919;
    --card-edge: #2a2a2a;
    --gold: #f3b80a;
    --gold-line: #b88a06;
  }
  * { margin: 0; padding: 0; box-sizing: border-box; }
  html, body {
    width: 1200px;
    height: 848px;
    overflow: hidden;
    background: var(--page-bg);
  }
  .canvas {
    width: 1200px;
    height: 848px;
    display: flex;
    align-items: center;
    justify-content: center;
    gap: 48px;
  }
  .card {
    position: relative;
    width: 540px;
    height: 309px;
    background: var(--card-bg);
    border: 1px solid var(--card-edge);
    color: var(--gold);
    font-family: "Roboto", sans-serif;
    font-weight: 300;
    box-shadow: 0 10px 24px rgba(0,0,0,0.18);
  }

  /* Front */
  .brand-name {
    font-family: "Roboto", sans-serif;
    font-weight: 400;
    color: var(--gold);
    letter-spacing: 0.5px;
    display: flex;
    align-items: center;
    gap: 10px;
  }
  .brand-mark {
    width: 12px;
    height: 12px;
    border-radius: 50%;
    background: var(--gold);
    flex: none;
  }
  .card-front .brand-name {
    position: absolute;
    left: 30px;
    top: 150px;
    font-size: 24px;
  }
  .divider {
    position: absolute;
    left: 300px;
    top: 34px;
    width: 1px;
    height: 240px;
    background: var(--gold-line);
  }
  .tagline {
    position: absolute;
    left: 318px;
    top: 30px;
    font-size: 26px;
    font-weight: 300;
  }
  .contact {
    position: absolute;
    left: 318px;
    top: 128px;
    right: 14px;
    list-style: none;
    font-size: 10.5px;
    line-height: 1.35;
    text-transform: uppercase;
    text-align: center;
  }
  .contact li { margin-bottom: 9px; }

  /* Back */
  .card-back .brand-name {
    position: absolute;
    left: 0;
    right: 0;
    top: 40px;
    justify-content: center;
    font-size: 28px;
  }
  .offers {
    position: absolute;
    left: 24px;
    right: 24px;
    top: 108px;
    list-style: none;
    text-align: center;
    text-transform: uppercase;
  }
  .offer { margin-bottom: 14px; }
  .offer-day {
    font-size: 14px;
    font-weight: 400;
    letter-spacing: 0.3px;
  }
  .offer-detail {
    font-size: 11px;
    margin-top: 3px;
  }
</style>
</head>
<body>
<main class="canvas">

  <section class="card card-front" aria-label="Business card front">
    <div class="brand-name"><span class="brand-mark"></span>Simply Swept Upward</div>
    <div class="divider"></div>
    <div class="tagline">Blow Dry Bar</div>
    <ul class="contact">
      <li>(555) 014-2763</li>
      <li>WWW.SIMPLYSWEPTUPWARD.EXAMPLE</li>
      <li>INFO@SIMPLYSWEPTUPWARD.EXAMPLE</li>
      <li>88 Heron Bend Drive Suite<br>4 Marlow Springs, Texas 75009</li>
    </ul>
  </section>

  <section class="card card-back" aria-label="Business card back">
    <div class="brand-name"><span class="brand-mark"></span>Simply Swept Upward</div>
    <ul class="offers">
      <li class="offer">
        <div class="offer-day">Monday Madness</div>
        <div class="offer-detail">10% off all products purchased in store</div>
      </li>
      <li class="offer">
        <div class="offer-day">Thrifty Tuesday</div>
        <div class="offer-detail">$5.00 off your blow out service when you add any one upper</div>
      </li>
      <li class="offer">
        <div class="offer-day">Winedown Wednesday</div>
        <div class="offer-detail">Bring a friend, 2 blow outs for $60.00+tax</div>
      </li>
    </ul>
  </section>

</main>
</body>
</html>
```